RW Holloway LLC Business Card - Civil Engineering & Consulting Firm

We need a Business Card that is elegant, and masculine.  It is our Professional Civil Engineering & Consulting Company located in San Antonio TX (Not s construction or builder firm- no gears & no tool images please). We provide civil engineering services including  commercial site plans, grading and drainage plans, utility plans, hydraulics and hydrology, land planning, utility coordination, and other general civil engineering services related to commercial and residential development.
We have 2 existing Logos. We would like to convey reliability, strength, trustworthiness and attention to detail.  Blues and orange tones as per logo We are OK with the use of a darker blue in the mix.  We have 2 logo versions - Full Company Name Logo to go on the back of card, & Small Icon Logo for the front w/ personal Info.

Target Market(s)
Architects, Real Estate Developers, Other Strctural Engineers, Surveyers, General Contractors
Industry/Entity Type
Professional Civil Engineering
Contact Information for Business Card
Name, Position, Address, Cell & Office #, email, and company website
Font styles to use
Other font styles liked:
- Avian
Requirements
Should not have
- No Tools, No Gears, no Cranes, or Construction Equipment.

```html
<!DOCTYPE html>
<html lang="en">
<head>
<meta charset="utf-8">
<title>RW Holloway LLC Business Card</title>
<link href="https://fonts.googleapis.com/css2?family=Arimo:wght@400&family=Raleway:wght@400&display=swap" rel="stylesheet">
<style>
  :root {
    --stage: #2e2e2e;
    --paper: #ffffff;
    --sky: #7aadd8;
    --sky-text: #6fa3d6;
    --orange: #f0922b;
    --ink: #4a4a4a;
    --white: #ffffff;
  }
  * { margin: 0; padding: 0; box-sizing: border-box; }
  html, body { width: 1075px; height: 1200px; overflow: hidden; background: var(--stage); }
  body { position: relative; font-family: "Arimo", Arial, sans-serif; }

  .card {
    position: absolute; left: 206px; width: 663px; height: 396px;
    box-shadow: 3px 3px 3px rgba(0,0,0,0.55);
    overflow: hidden;
  }
  .card--front { top: 187px; background: var(--paper); }
  .card--back { top: 637px; background: var(--sky); }

  .brand {
    position: absolute; display: flex; align-items: center; gap: 14px;
    font-family: "Arimo", Arial, sans-serif; font-weight: 400;
    letter-spacing: 3px; white-space: nowrap;
  }
  .brand__mark { display: block; }
  .card--front .brand { right: 40px; top: 88px; font-size: 30px; color: var(--sky-text); }
  .card--front .brand__mark { width: 22px; height: 22px; background: var(--orange); }
  .card--back .brand { left: 50%; transform: translateX(-50%); top: 138px; font-size: 40px; color: var(--white); }
  .card--back .brand__mark { width: 28px; height: 28px; border: 3px solid var(--white); }

  .person { position: absolute; left: 36px; top: 193px; }
  .person__name { font-family: "Raleway", Arial, sans-serif; font-size: 25px; letter-spacing: 0.5px; line-height: 1.1; color: var(--sky-text); }
  .person__name .surname { color: var(--orange); }
  .person__title { font-size: 17px; color: var(--ink); margin-top: 3px; }
  .person__rule { position: absolute; left: 36px; top: 257px; width: 214px; height: 5px; background: var(--orange); }

  .info-band { position: absolute; left: 0; top: 260px; width: 100%; height: 136px; background: var(--sky); color: var(--white); }
  .contact { position: absolute; left: 35px; top: 34px; list-style: none; font-size: 18px; line-height: 24px; }
  .contact li { display: flex; align-items: center; gap: 6px; }
  .contact svg { width: 18px; height: 18px; flex: none; }
  .address { position: absolute; right: 41px; top: 67px; text-align: right; font-size: 18px; line-height: 24px; font-style: normal; }

  .tagline { position: absolute; left: 0; width: 100%; top: 325px; text-align: center; font-size: 18px; color: var(--white); }
</style>
</head>
<body>

<section class="card card--front">
  <div class="brand"><span class="brand__mark"></span>RW HOLLOWAY LLC</div>

  <div class="person">
    <p class="person__name">DANIEL <span class="surname">REYES</span></p>
    <p class="person__title">Managing Director</p>
  </div>
  <div class="person__rule"></div>

  <div class="info-band">
    <ul class="contact">
      <li>
        <svg viewBox="0 0 20 20" aria-hidden="true"><path d="M5 2l3 4-2 2c1 2 3 4 5 5l2-2 4 3-2 3C9 17 3 11 2 5z" fill="none" stroke="#fff" stroke-width="1.6" stroke-linejoin="round"/></svg>
        210-555 014 732
      </li>
      <li>
        <svg viewBox="0 0 20 20" aria-hidden="true"><rect x="1.5" y="4" width="17" height="12" fill="#fff"/><path d="M1.5 4l8.5 7 8.5-7" fill="none" stroke="#7aadd8" stroke-width="1.4"/></svg>
        office@rwholloway.com
      </li>
      <li>
        <svg viewBox="0 0 20 20" aria-hidden="true"><g fill="none" stroke="#fff" stroke-width="1.5"><circle cx="10" cy="10" r="8"/><ellipse cx="10" cy="10" rx="3.5" ry="8"/><path d="M2 10h16M3.5 6h13M3.5 14h13"/></g></svg>
        www.rwholloway.com
      </li>
    </ul>
    <address class="address">2200 Alamo Ridge Drive<br>San Antonio, TX 78205</address>
  </div>
</section>

<section class="card card--back">
  <div class="brand"><span class="brand__mark"></span>RW HOLLOWAY LLC</div>
  <p class="tagline">Commercial and Residential Development</p>
</section>

</body>
</html>
```